OWNERS HANDBOOK

Take a MICROSOFT WORD document and turn it into a nicely designed and structured PDF or similar to circulate to Owners and to make available online for Owners to access.

```html
<!DOCTYPE html>
<html lang="en">
<head>
<meta charset="utf-8">
<title>Owner Handbook 2023 – Spreads</title>
<link href="https://fonts.googleapis.com/css2?family=PT+Sans+Narrow:wght@400;700&display=swap" rel="stylesheet">
<style>
  :root{
    --navy:#2a3a8c;
    --green:#8cc63f;
    --green-dark:#5e8f2a;
    --text:#333;
    --rule:#c9c9c9;
    --alert:#e0245e;
    --map-green:#1f9a4a;
  }
  *{box-sizing:border-box;margin:0;padding:0}
  html,body{width:1200px;height:475px;overflow:hidden;background:#fff}
  body{position:relative;font-family:"PT Sans Narrow",Arial Narrow,sans-serif;color:var(--text)}
  .page{position:absolute;top:19px;width:264px;height:373px;border:0.6px solid var(--green);background:#fff;overflow:hidden}
  .page--13{left:19px}.page--14{left:304px}.page--15{left:594px}.page--16{left:900px}
  .page-header{position:relative;height:53px}
  .header-photo{position:absolute;inset:0;background:linear-gradient(90deg,#6f9a3c 0%,#8fb45a 40%,#a9c27e 70%,#c6d2a6 100%)}
  .header-title{position:absolute;left:19px;top:18px;color:#fff;font-weight:700;font-size:6.2px;line-height:9px;letter-spacing:.1px}
  .page-body{padding:8px 19px 0 19px}
  h2{color:var(--navy);font-size:6px;font-weight:700;margin:5px 0 2.5px}
  h2:first-child{margin-top:0}
  p{font-size:4.4px;line-height:6.3px;text-indent:4px;margin-bottom:2.5px}
  .contact-list{list-style:none;font-size:4.4px;line-height:6.3px}
  .contact-list li{display:flex;border-bottom:0.5px solid var(--rule);padding:1.2px 0}
  .contact-list li::before{content:"";width:3.5px;height:3.5px;background:var(--navy);margin:1.4px 5px 0 0;flex:none}
  .contact-name{width:53px}
  .alert-heading{color:var(--alert)}
  .alert-text{color:var(--alert);text-transform:uppercase;text-indent:4px}
  .caps{text-transform:uppercase;font-size:4.2px}
  .appendix-title{color:var(--navy);font-size:9.6px;font-weight:700;margin-bottom:3px}
  .appendix-rule{height:1.8px;background:linear-gradient(90deg,var(--green) 0%,var(--green) 60%,rgba(140,198,63,0) 100%);margin-bottom:8px}
  .page-number{position:absolute;right:0;bottom:0;width:21px;height:13px;background:var(--green);color:#333;font-size:4.6px;padding:2px 0 0 4px}
  .evac-map{background:var(--map-green);padding:5px 2px 3px;margin-bottom:5px}
  .evac-map__title{color:#fff;font-weight:700;font-size:5.2px;text-align:center;margin-bottom:4px;font-family:Arial,sans-serif}
  .evac-map__plan{height:66px;background:linear-gradient(135deg,#f4f7f1,#e7efe0)}
  .evac-map__band{color:#fff;font-size:3.2px;text-align:center;font-weight:700;margin:2px 0;font-family:Arial,sans-serif}
  .evac-map__legend{height:35px;background:#f6f6f6}
</style>
</head>
<body>

<section class="page page--13">
  <header class="page-header">
    <div class="header-photo" role="img" aria-label="Photo of a palm-lined resort street"></div>
    <div class="header-title">VALE LUZ VILLAGE AND VILLAGE GARDENS<br>OWNER HANDBOOK 2023</div>
  </header>
  <div class="page-body">
    <h2>Café’s within the resort</h2>
    <ul class="contact-list">
      <li><span class="contact-name">Vale Luz Café</span>+351 960 000 111 (dine in and takeaway service available)</li>
      <li><span class="contact-name">Café da Esquina</span>+351 960 000 222 (dine in and takeaway service available)</li>
    </ul>
    <h2>Supermarket</h2>
    <p>We have a small supermarket Mercadinho Sol within the resort (next to the Vale Luz Café)</p>
    <h2>Hairdressers within the complex:</h2>
    <ul class="contact-list">
      <li><span class="contact-name">Hair and Beauty Salon</span>+351 910 000 333</li>
      <li><span class="contact-name">Salão Marisa</span>+351 910 000 444</li>
    </ul>
    <h2>Serra Mar Hotel and Golf Course</h2>
    <p>A short drive and not too far walk away is the Serra Mar Hotel and Golf club.</p>
    <p>Vale Luz Owners receive a discount for golf at the club and please ensure you show the reception desk your Vale Luz Owners card with up-to-date year label on the card. Please note the Owners card is available from Customer Service Offices at Coastline Living office (beside Harbour Pub).</p>
    <h2>Communal WIFI</h2>
    <p>A communal WIFI service is provided in the Gardens Area next to the main pool Area for all Owners and their guest to use.</p>
    <p>Username and Passwords are updated regularly, and full details can be obtained from staff working in the Bar area of the Gardens.</p>
    <h2>Waste Disposal</h2>
    <p>Owners are responsible for the proper use of the Condominium waste disposal bins strategically placed near each apartment block by the Waste disposal company Limpamar.</p>
    <p>Please remember to ensure you separate Plastics and glass from the general waste you are disposing.</p>
    <h2>Cash Machines (ATM)</h2>
    <p>There are 2 ATM machines in our area, one is beside Harbour pub and the other one in between the Bistro and the Supermarket.</p>
    <h2>Air Conditioning</h2>
    <p>The majority if not all the Apartments are using A/C within the apartment. It is advisable to have your respective A/C units and chiller serviced on a regular basis. There are quite a few local A/C maintenance service providers, including:</p>
    <ul class="contact-list">
      <li><span class="contact-name">Frescoterm -</span>+351 289 000 555</li>
      <li><span class="contact-name">Polar Air -</span>+351 289 000 666</li>
    </ul>
  </div>
  <div class="page-number">13</div>
</section>

<section class="page page--14">
  <header class="page-header">
    <div class="header-photo" role="img" aria-label="Photo of a palm-lined resort street"></div>
    <div class="header-title">VALE LUZ VILLAGE AND VILLAGE GARDENS<br>OWNER HANDBOOK 2023</div>
  </header>
  <div class="page-body">
    <h2>Electricity Supply</h2>
    <p>In many parts of the Algarve, intermittent and disrupted electrical supply can occur, this may require in some instances for the Owner to call Security. Access to the Services cupboard on the ground floor in each block, (where the individual electricity meters are located) is through the key provided to each apartment or alternatively by contacting Security who can open the services doors.</p>
    <h2>Apartment Alarms</h2>
    <p>A number of apartments have alarms connected to the Guarda Sete security centre situated in the security office opposite the Ember restaurant and near to B0 block.</p>
    <p>If you are leaving your apartment for any period of time, we strongly recommend you advise the Property Management company – Customer Services and advise them if your alarm is on.</p>
    <h2>Pool and Gardens Maintenance</h2>
    <p>The Gardens and Pool maintenance is outsourced to a local company who are responsible for the upkeep of every aspect of the Gardens and Pools and similarly in all common areas surrounding and attached to our complex.</p>
    <p>Throughout the year you will hear and see the gardening or Pool staff at work, keeping our Gardens beautiful.</p>
    <h2>Pest control</h2>
    <p>We have continual Pest Control programme in place and in particular for dealing with the processionary caterpillars that become evident in the early spring of each year. If you see a procession near your apartment block or in the Gardens area, PLEASE ALERT THE PROPERTY MANAGEMENT COMPANY ASAP!</p>
    <h2 class="alert-heading">Fire Safety</h2>
    <p class="alert-text">Should you detect a fire in your apartment, block, common areas or gardens alert security and please call 112 for the bombedeiros who will arrive to deal with the issue.</p>
    <p class="caps">Full fire evacuation procedures are contained within appendix 2 of this handbook.</p>
    <h2>Public Transport</h2>
    <p>Public buses run on the N398 main road adjoining the entrance to Vale Luz, bus stops are on both sides of the N398 (the main road outside the complex).</p>
    <p>Trains are available and nearest stations are at Faro, Loule and Almancil.</p>
  </div>
  <div class="page-number">14</div>
</section>

<section class="page page--15">
  <header class="page-header">
    <div class="header-photo" role="img" aria-label="Photo of a palm-lined resort street"></div>
    <div class="header-title">VALE LUZ VILLAGE AND VILLAGE GARDENS<br>OWNER HANDBOOK 2023</div>
  </header>
  <div class="page-body">
    <h1 class="appendix-title">APPENDIX 1 – PEAK SEASON PROCEDURES</h1>
    <div class="appendix-rule"></div>
    <h2>Peak Season procedure for visitors to Village Gardens Club (VGC)</h2>
    <p>The High Season Procedure (HSP) will be triggered when necessary whenever the volume and demand for sunbeds is high. An Email will be sent to owners informing them when the procedure will commence. When the HSP is activated then sunbeds will be allocated by the pool attendants when shown the sunbed tokens.</p>
    <p>Please do not use towels or other personal items in order to “reserve sunbeds”. These will be removed by the Pool Attendant.</p>
    <h2>Pool Attendants</h2>
    <p>During the summer months from July to September there will be pool attendants to assist with any queries or issues and also to manage the sunbed allocation when necessary.</p>
    <p>At the peak period there will be two pool attendants every day, one of whom will be at the Pool Attendant post at the Central pool at all times from the hours of 10:00 to 19:00.</p>
    <p>Pool attendants are also instructed to remove towels etc. from unoccupied sunbeds. If you do find your towels have been removed, then please go to the pool attendant who will return them to you.</p>
    <h2>Sunbed tokens</h2>
    <p>All Apartments will be provided with Sunbed tokens. These will need to be shown to the Pool Attendants if and when the High Season Procedure (HSP) is triggered.</p>
    <p>The tokens can be collected from customer services. (5 for 2-bedroom and 7 for 3-bedroom apartments)</p>
    <p>If tokens are lost, then please report it to customer services and replacements can be provided at a cost of 2 Euros per token.</p>
    <h2>North Pool</h2>
    <p>The North pool (near to B14 and B15) has been designated as a swimming only pool. Inflatables are therefore not permitted at this pool at any time.</p>
    <h2>Inflatables</h2>
    <p>Inflatables are permitted in the central and lower pools. We do however ask that you respect other visitors when using them in and around the pool areas. Inflatables should be removed from the pool when not in use.</p>
    <h2>Queries or Complaints</h2>
    <p>In the first instance please report any concerns to the Pool Attendant. If not resolved, then ring the PMC Help number 289 000 777.</p>
    <p>IMPORTANT NOTE: abuse of the pool attendants is unacceptable. They have been instructed to report any abuse to security and PMC.</p>
  </div>
  <div class="page-number">15</div>
</section>

<section class="page page--16">
  <header class="page-header">
    <div class="header-photo" role="img" aria-label="Photo of a palm-lined resort street"></div>
    <div class="header-title">VALE LUZ VILLAGE AND VILLAGE GARDENS<br>OWNER HANDBOOK 2023</div>
  </header>
  <div class="page-body">
    <h1 class="appendix-title">APPENDIX 2 – FIRE EVACUATION PROCEDURES</h1>
    <div class="appendix-rule"></div>
    <div class="evac-map">
      <div class="evac-map__title">PLANTA DE EMERGÊNCIA - PLAN D’ÉVACUATION - EVACUATION MAP</div>
      <div class="evac-map__plan" role="img" aria-label="Evacuation plan of the upper blocks with escape routes and fire equipment"></div>
      <div class="evac-map__band">EM CASO DE INCÊNDIO - EN CAS D’INCENDIE - IN CASE OF FIRE</div>
      <div class="evac-map__legend" role="img" aria-label="Fire instructions in Portuguese, French and English with symbol legend"></div>
    </div>
    <div class="evac-map">
      <div class="evac-map__title">PLANTA DE EMERGÊNCIA - PLAN D’ÉVACUATION - EVACUATION MAP</div>
      <div class="evac-map__plan" role="img" aria-label="Evacuation plan of the lower blocks with escape routes and fire equipment"></div>
      <div class="evac-map__band">EM CASO DE INCÊNDIO - EN CAS D’INCENDIE - IN CASE OF FIRE</div>
      <div class="evac-map__legend" role="img" aria-label="Fire instructions in Portuguese, French and English with symbol legend"></div>
    </div>
  </div>
  <div class="page-number">16</div>
</section>

</body>
</html>
```